Business Card Design For Financial Company

Create a new design for company's business card. The corporate logo is attached in several formats. Our new website design is also attached and we would like the business cards to reflect this.
Card needs to contain the following info:
Name
Job Title
Legal company name - eg Varo-Q Capital (Asia) Ltd
Address - eg 612-09 Belmore Plaza,47 Tamsin Street, Hong Kong
Direct tel
Main tel
Fax
Email
Website URL
MS word format preferred. Other formats that can be edited on standard PC also OK.
Updates
Please note the the "VARO-Q" logo nameĀ font is "Gill Sans MT" on Windows
Target Market(s)
Instituation Investors
Industry/Entity Type
Business
Look and feel

```html
<!DOCTYPE html>
<html lang="en">
<head>
<meta charset="utf-8">
<title>Varo-Q Capital Business Card</title>
<link rel="stylesheet" href="https://fonts.googleapis.com/css2?family=Lato:wght@300;400&display=swap">
<style>
  :root {
    --backdrop: #97a2a8;
    --brand-red: #d30f1e;
    --brand-deep: #7d0000;
    --card-white: #ffffff;
    --ink: #1e1e1e;
    --ink-soft: #2b2b2b;
    --shadow: rgba(0, 0, 0, 0.85);
  }
  * { margin: 0; padding: 0; box-sizing: border-box; }
  html, body {
    width: 1200px;
    height: 900px;
    overflow: hidden;
    background: var(--backdrop);
    font-family: "Lato", sans-serif;
  }
  .canvas { position: relative; width: 1200px; height: 900px; }
  .card {
    position: absolute;
    left: 335px;
    width: 608px;
    height: 372px;
    border-radius: 28px;
    box-shadow: 6px 6px 3px var(--shadow);
  }
  .card--front { top: 60px; background: var(--brand-red); }
  .card--back { top: 459px; height: 371px; background: var(--card-white); color: var(--ink-soft); }

  .front-mark {
    position: absolute;
    left: 251px;
    top: 103px;
    width: 100px;
    height: 100px;
    border-radius: 50%;
    background: var(--brand-deep);
  }
  .front-name {
    position: absolute;
    left: 0;
    right: 0;
    top: 212px;
    text-align: center;
    font-size: 52px;
    font-weight: 300;
    letter-spacing: 1px;
    color: var(--card-white);
  }

  .back-mark {
    position: absolute;
    left: 506px;
    top: 40px;
    width: 60px;
    height: 60px;
    border-radius: 50%;
    background: var(--brand-deep);
  }
  .person { position: absolute; left: 42px; top: 36px; font-size: 19px; line-height: 26px; }
  .person__name { font-weight: 400; color: var(--ink); }
  .person__title { font-weight: 300; }

  .company { position: absolute; left: 42px; top: 176px; font-size: 19px; line-height: 26px; font-weight: 300; }

  .contact { position: absolute; top: 256px; font-size: 19px; line-height: 25.5px; font-weight: 300; }
  .contact--phones { left: 42px; }
  .contact--web { left: 285px; }
</style>
</head>
<body>
<main class="canvas">
  <section class="card card--front" aria-label="Card front">
    <div class="front-mark"></div>
    <div class="front-name">VARO-Q</div>
  </section>

  <section class="card card--back" aria-label="Card back">
    <div class="back-mark"></div>
    <div class="person">
      <p class="person__name">Daniel Hartley</p>
      <p class="person__title">Sales Manager</p>
    </div>
    <div class="company">
      <p>Varo-Q Capital (Asia) Ltd</p>
      <p>612-09 Belmore Plaza, 47 Tamsin Street, Hong Kong</p>
    </div>
    <div class="contact contact--phones">
      <p>main tel: 318 552 0947</p>
      <p>direct tel: 427 960 3158</p>
      <p>fax: 031 486 2275</p>
    </div>
    <div class="contact contact--web">
      <p>contact@varoqcapital.com</p>
      <p>www.varoqcapital.com</p>
    </div>
  </section>
</main>
</body>
</html>
```